Brenwick Structures Construction Company Seeking Modern Website

We are a small construction company wanting to create a web presence. We don't have much in the way of current content but will get photos as they come in. Attached is a picture of our business card.
The pages we would like on the menu are:
Home
Portfolio
Product Specs
Testimonials
Our Process
Contact
Some designs we like are:
http://www.tovasheds-example.com/
http://www.qrnstructures-example.com/
http://dunholtbarns-example.com/
http://pellingframes-example.com/
Not much requirements other than that so feel free to be creative!
Updates
Target Market(s)
Construction
Commercial and Residential Buildings
Industry/Entity Type
Construction Company
Number of Pages Required
5+ page
Look and feel

```html
<!DOCTYPE html>
<html lang="en">
<head>
<meta charset="utf-8">
<title>Brenwick Structures</title>
<link href="https://fonts.googleapis.com/css2?family=Raleway:wght@400;500;600;700&family=Open+Sans:wght@400;600&display=swap" rel="stylesheet">
<style>
:root{
  --red:#d6261f;
  --blue:#0aa2e0;
  --teal:#1f6f92;
  --ink:#333333;
  --muted:#8a8a8a;
  --line:#e1e1e1;
  --pale:#f6f6f6;
  --footer:#221e1f;
  --footer-bar:#141213;
  --white:#ffffff;
}
*{margin:0;padding:0;box-sizing:border-box}
html,body{width:1200px;height:3046px;overflow:hidden}
body{position:relative;background:var(--white);font-family:"Raleway",sans-serif;color:var(--ink)}
.abs{position:absolute}
.photo{position:absolute}
.body-copy{font-family:"Open Sans",sans-serif;font-size:12px;line-height:20px;color:var(--muted)}
.read-more{font-size:14px;color:var(--red);text-decoration:none}

/* header */
.site-header{position:absolute;left:0;top:0;width:1200px;height:146px;background:var(--white)}
.brand{position:absolute;left:55px;top:56px;display:flex;align-items:center;gap:10px;font-size:30px;font-weight:700;color:var(--red)}
.brand-mark{width:22px;height:22px;border-radius:50%;background:var(--red)}
.main-nav{position:absolute;top:66px;font-size:14px}
.main-nav a{position:absolute;white-space:nowrap;color:var(--ink);text-decoration:none}
.main-nav a.active{color:var(--red)}

/* hero */
.hero{position:absolute;left:0;top:146px;width:1200px;height:514px;background:linear-gradient(180deg,#9a8b74 0%,#c7b690 35%,#6d6452 70%,#3c3a33 100%)}
.hero-title{position:absolute;left:95px;top:180px;font-size:50px;font-weight:500;color:var(--red)}
.hero-sub{position:absolute;left:95px;top:248px;font-size:32px;line-height:52px;color:var(--white)}
.hero-arrows{position:absolute;left:468px;top:305px;display:flex;gap:4px}
.hero-arrows span{width:20px;height:20px;border-radius:50%;border:1px solid #ddd;background:rgba(255,255,255,.35)}

/* band */
.expert-band{position:absolute;left:0;top:660px;width:1200px;height:97px;background:var(--blue)}
.expert-band p{position:absolute;left:125px;top:36px;font-size:21px;color:var(--white)}
.btn-outline{position:absolute;left:877px;top:28px;width:200px;height:42px;border:1px solid var(--white);color:var(--white);font-size:20px;text-align:center;line-height:40px}

/* services */
.service-title{position:absolute;font-size:17px;color:var(--ink)}
.service-text{position:absolute;width:320px}

/* specialities */
.specialities{position:absolute;left:0;top:1272px;width:1200px;height:533px;background:var(--pale)}
.tab{position:absolute;top:78px;height:47px;line-height:47px;font-size:16px}
.tab-active{left:97px;width:300px;background:var(--blue);color:var(--white);padding-left:32px;clip-path:polygon(0 0,85% 0,100% 100%,0 100%)}
.tab-idle{left:350px;width:350px;background:#dcdcdc;color:var(--ink);padding-left:92px;clip-path:polygon(0 0,88% 0,100% 100%,14% 100%)}
.spec-card{position:absolute;left:97px;top:165px;width:690px;height:280px;background:var(--white);border:1px solid var(--line)}
.spec-card h3{position:absolute;left:368px;top:40px;font-size:17px;font-weight:500}
.spec-card .body-copy{position:absolute;left:368px;top:78px;width:292px;text-align:justify}
.spec-card .read-more{position:absolute;left:368px;top:220px}
.feature{position:absolute;left:833px;display:flex;align-items:center;gap:30px;font-size:20px;color:#555}
.feature-icon{width:72px;height:72px;border-radius:50%;background:var(--red);border:3px solid #f0c4c2;display:flex;align-items:center;justify-content:center}

/* projects */
.projects{position:absolute;left:0;top:1805px;width:1200px;height:468px;background:linear-gradient(180deg,#2a7fa3,#1c6b8f 60%,#1a5f80)}
.projects h2{position:absolute;left:95px;top:60px;font-size:26px;font-weight:500;color:var(--white)}
.project-filter{position:absolute;left:433px;top:48px;width:670px;height:52px;border-top:1px solid rgba(255,255,255,.5);border-bottom:1px solid rgba(255,255,255,.5)}
.project-filter span{position:absolute;top:17px;font-size:13px;color:var(--white)}
.round-arrow{position:absolute;width:18px;height:18px;border-radius:50%;border:1px solid rgba(255,255,255,.7)}
.tool{position:absolute;left:290px;width:47px;height:47px;background:var(--blue);display:flex;align-items:center;justify-content:center}

/* testimonials */
.testimonials h2{position:absolute;left:95px;top:2333px;font-size:26px;font-weight:500}
.quote-card{position:absolute;top:2400px;width:480px;height:113px;border:1px solid var(--line);padding:18px 28px;text-align:justify}
.avatar{position:absolute;top:2525px;width:90px;height:90px;border-radius:50%;border:3px solid var(--white);box-shadow:0 0 0 1px var(--line)}
.quote-name{position:absolute;top:2530px;font-size:15px}

/* footer */
.site-footer{position:absolute;left:0;top:2685px;width:1200px;height:305px;background:var(--footer);color:var(--white)}
.site-footer h4{position:absolute;top:50px;font-size:26px;font-weight:500}
.footer-copy{font-family:"Open Sans",sans-serif;font-size:11px;line-height:19px;color:#a9a9a9}
.social{position:absolute;left:100px;top:232px;display:flex;gap:6px}
.social span{width:20px;height:20px;border-radius:50%}
.contact-row{position:absolute;left:512px;display:flex;gap:28px;align-items:flex-start}
.email-field{position:absolute;left:855px;top:152px;width:230px;border-bottom:1px solid #555;padding-bottom:8px;font-size:12px;color:#777}
.btn-send{position:absolute;left:855px;top:200px;width:98px;height:32px;background:var(--red);color:var(--white);font-size:14px;text-align:center;line-height:32px}
.footer-bar{position:absolute;left:0;top:2990px;width:1200px;height:56px;background:var(--footer-bar);color:#ccc;font-size:13px}
</style>
</head>
<body>

<header class="site-header">
  <div class="brand"><span class="brand-mark"></span>Brenwick Structures</div>
  <nav class="main-nav">
    <a class="active" style="left:418px">Home</a>
    <a style="left:515px">Portfolio</a>
    <a style="left:625px">Product Specs</a>
    <a style="left:775px">Testimonials</a>
    <a style="left:915px">Our Process</a>
    <a style="left:1048px">Contact</a>
  </nav>
</header>

<section class="hero" role="img" aria-label="Tower cranes over a rising building site against a cloudy golden sky">
  <h1 class="hero-title">Brenwick Structures</h1>
  <p class="hero-sub">Buliding Dreams, So You<br>Can Build Memories</p>
  <div class="hero-arrows"><span></span><span></span></div>
</section>

<section class="expert-band">
  <p>We are the Expert on this Field, Better construction Since The Year</p>
  <div class="btn-outline">Conatct Us</div>
</section>

<section class="services">
  <div class="photo" style="left:97px;top:830px;width:258px;height:185px;background:linear-gradient(180deg,#5e9ec8,#a9c2d0 55%,#b59b6e)" role="img" aria-label="Crane over a construction site under blue sky"></div>
  <h3 class="service-title" style="left:97px;top:1040px">Harlan Dovecote</h3>
  <p class="service-text body-copy" style="left:97px;top:1070px;width:310px">There are many variations of passages of Lorem Ipsum available, but the majority have suffered alteration in some form, by injected humour, or randomised words which don't look even slightly believable.</p>
  <a class="read-more abs" style="left:97px;top:1168px">Read More</a>

  <h3 class="service-title" style="left:443px;top:828px">Bonorum et Malorum</h3>
  <p class="service-text body-copy" style="left:443px;top:858px;width:310px">There are many variations of passages of Lorem Ipsum available, but the majority have suffered alteration in some form, by injected humour, or randomised words which don't look even slightly believable.</p>
  <a class="read-more abs" style="left:443px;top:958px">Read More</a>
  <div class="photo" style="left:443px;top:1002px;width:314px;height:185px;background:linear-gradient(160deg,#4a6f8a,#9fb3c0 50%,#d8a640 80%,#5b5b5b)" role="img" aria-label="Excavator digging on a snowy site"></div>

  <div class="photo" style="left:787px;top:830px;width:313px;height:185px;background:linear-gradient(180deg,#8ab0cc,#d59a55 55%,#2b241e)" role="img" aria-label="Workers silhouetted on steel frame at sunset"></div>
  <h3 class="service-title" style="left:787px;top:1040px">Corporis Suscipit</h3>
  <p class="service-text body-copy" style="left:787px;top:1070px;width:310px">There are many variations of passages of Lorem Ipsum available, but the majority have suffered alteration in some form, by injected humour, or randomised words which don't look even slightly believable.</p>
  <a class="read-more abs" style="left:787px;top:1168px">Read More</a>
</section>

<section class="specialities">
  <div class="tab tab-idle">Residential Buildings</div>
  <div class="tab tab-active">Commercial Construction</div>
  <div class="spec-card">
    <div class="photo" style="left:0;top:0;width:336px;height:278px;background:linear-gradient(180deg,#e8c79a,#b9a48a 45%,#34506a)" role="img" aria-label="City towers and cranes at dusk"></div>
    <h3>Commercial Construction</h3>
    <p class="body-copy">Many desktop publishing packages and web page editors now use Lorem Ipsum as their default model text, and a search for 'lorem ipsum' will uncover many web sites still in their infancy. Various versions have evolved over the years, sometimes by accident, sometimes on purpose</p>
    <a class="read-more">Read More</a>
  </div>
  <div class="feature" style="top:160px">
    <span class="feature-icon"><svg width="34" height="26" viewBox="0 0 34 26" fill="none" stroke="#fff" stroke-width="2.5"><rect x="5" y="2" width="24" height="16" rx="1"/><path d="M1 23h32"/></svg></span>Good Planning</div>
  <div class="feature" style="top:264px">
    <span class="feature-icon"><svg width="36" height="28" viewBox="0 0 36 28" fill="#fff"><circle cx="18" cy="7" r="5"/><circle cx="7" cy="10" r="4"/><circle cx="29" cy="10" r="4"/><path d="M9 27c0-7 4-12 9-12s9 5 9 12z"/><path d="M0 27c0-6 3-10 7-10 2 0 3 1 4 2-2 2-3 5-3 8z"/><path d="M36 27c0-6-3-10-7-10-2 0-3 1-4 2 2 2 3 5 3 8z"/></svg></span>Awesome Stuff</div>
  <div class="feature" style="top:367px">
    <span class="feature-icon"><svg width="24" height="32" viewBox="0 0 24 32" fill="#fff"><path d="M2 2h20v30H2z"/><g fill="#d6261f"><rect x="6" y="6" width="4" height="4"/><rect x="14" y="6" width="4" height="4"/><rect x="6" y="13" width="4" height="4"/><rect x="14" y="13" width="4" height="4"/><rect x="6" y="20" width="4" height="4"/><rect x="14" y="20" width="4" height="4"/><rect x="10" y="27" width="4" height="5"/></g></svg></span>Construction</div>
</section>

<section class="projects">
  <h2>Recent Projects</h2>
  <div class="project-filter">
    <span style="left:53px">All Projects</span>
    <span style="left:182px">Design</span>
    <span style="left:292px">Buildings</span>
    <span style="left:412px">Constructions</span>
    <span style="left:560px">Isolations</span>
  </div>
  <span class="round-arrow" style="left:66px;top:283px"></span>
  <span class="round-arrow" style="left:1110px;top:283px"></span>
  <div class="photo" style="left:97px;top:158px;width:240px;height:244px;background:linear-gradient(200deg,#fbe6c0,#e9cfc8 40%,#c6ccd8)" role="img" aria-label="Steel structure in bright sunlight"></div>
  <div class="tool" style="top:158px"><svg width="18" height="18" viewBox="0 0 18 18" fill="none" stroke="#fff" stroke-width="2.5"><circle cx="7" cy="7" r="5"/><path d="M11 11l6 6"/></svg></div>
  <div class="tool" style="top:205px;background:#4fb5de"><svg width="20" height="12" viewBox="0 0 20 12" fill="#fff"><path d="M10 0C5 0 1 6 1 6s4 6 9 6 9-6 9-6-4-6-9-6z"/><circle cx="10" cy="6" r="2.5" fill="#4fb5de"/></svg></div>
  <div class="photo" style="left:353px;top:158px;width:240px;height:244px;background:linear-gradient(180deg,#6aa4d6,#b5c2c6 50%,#9a8f7c)" role="img" aria-label="Multi-storey building under construction"></div>
  <div class="photo" style="left:607px;top:158px;width:240px;height:244px;background:linear-gradient(135deg,#dfe9f2,#6f97b8 50%,#1f3a55)" role="img" aria-label="Glass skyscraper seen from below"></div>
  <div class="photo" style="left:861px;top:158px;width:240px;height:244px;background:linear-gradient(180deg,#3f78c4,#9fb4c4 45%,#8a4b3a 70%,#6f7a5a)" role="img" aria-label="Modern office building with glass facade"></div>
</section>

<section class="testimonials">
  <h2>Testimonial</h2>
  <span class="round-arrow" style="left:66px;top:2482px;border-color:#ccc"></span>
  <span class="round-arrow" style="left:1110px;top:2482px;border-color:#ccc"></span>
  <div class="quote-card body-copy" style="left:97px">"Lorem Ipsum is not simply random text. It has roots in a piece of classical Latin literature from 45 BC, making it over 2000 years old. Harlan Dovecote, a Latin professor at Westmere Ridge College in Virginia, looked up one of the more obscure Latin words"</div>
  <div class="avatar" style="left:132px;background:linear-gradient(180deg,#c9c3bb,#8d7763)" role="img" aria-label="Portrait of a client"></div>
  <span class="quote-name" style="left:248px">- Bonorum et Malorum</span>
  <div class="quote-card body-copy" style="left:623px">"Lorem Ipsum is not simply random text. It has roots in a piece of classical Latin literature from 45 BC, making it over 2000 years old. Harlan Dovecote, a Latin professor at Westmere Ridge College in Virginia, looked up one of the more obscure Latin words"</div>
  <div class="avatar" style="left:655px;background:linear-gradient(180deg,#d8d2c8,#b98b5e)" role="img" aria-label="Portrait of a client"></div>
  <span class="quote-name" style="left:772px">- Bonorum et Malorum</span>
</section>

<footer class="site-footer">
  <h4 style="left:100px">About us</h4>
  <p class="footer-copy abs" style="left:100px;top:104px;width:342px;text-align:justify">a Latin professor at Westmere Ridge College in Virginia, looked up one of the more obscure Latin words, consectetur, from a Lorem Ipsum passage, and going through the cites of the word in classical literature, discovered the undoubtable source. Lorem Ipsum comes from sections</p>
  <div class="social"><span style="background:#29a9e1"></span><span style="background:#f39c12"></span><span style="background:#3b5998"></span><span style="background:#cb2027"></span><span style="background:#666"></span></div>

  <h4 style="left:512px">Get In Touch</h4>
  <div class="contact-row" style="top:106px"><svg width="10" height="14" viewBox="0 0 10 14" fill="#d6261f"><path d="M5 0a5 5 0 015 5c0 4-5 9-5 9S0 9 0 5a5 5 0 015-5z"/><circle cx="5" cy="5" r="2" fill="#221e1f"/></svg><p class="footer-copy" style="width:280px">200 Latin words, combined with a handful of model sentence structures</p></div>
  <div class="contact-row" style="top:155px"><svg width="12" height="12" viewBox="0 0 12 12" fill="#d6261f"><path d="M2 0l3 3-1.5 2a7 7 0 003.5 3.5L9 7l3 3-2 2C5 12 0 7 0 2z"/></svg><p class="footer-copy">5550142210 / 5550187634</p></div>
  <div class="contact-row" style="top:192px"><svg width="14" height="10" viewBox="0 0 14 10" fill="none" stroke="#d6261f" stroke-width="1.5"><rect x="1" y="1" width="12" height="8"/><path d="M1 1l6 5 6-5"/></svg><p class="footer-copy">info@brenwickstructures-example.com</p></div>

  <h4 style="left:855px">Newsletter</h4>
  <p class="footer-copy abs" style="left:855px;top:104px;width:240px">Subscribe to Newsletters for more information and updates</p>
  <div class="email-field">Email id</div>
  <div class="btn-send">Send Now</div>
</footer>

<div class="footer-bar">
  <span class="abs" style="left:97px;top:20px">Copyrights@Brenwick Structures2015</span>
  <span class="abs" style="left:1100px;top:20px">C15</span>
</div>

</body>
</html>
```